4th Generation Family Business Needs a New Card Design!

We are a family owned 4th Generation company. We are based in the Sydney, Australia area and we are desperately in need of a more modern and classy card. We are monumental masons who design, supply & erect lasting memorials throughout cemeteries in Sydney. Our customers are normally in a period of grieving. I have attached logo files that will need to be implemented on the card. Company was established 1935. Australian Owned and Operated. Card needs to be designed to PIXO.com specification.

Target Market(s)

Our target market is based upon people that a grieving for family members that have passed away. We also deal with alot of companies that own and operate cemeteries.

Industry/Entity Type

Business

Contact Information for Business Card

Simon Harcourt, Operations Manager, 0417293086, simon@harcourtmemorials.com.au
Lewis Harcourt, Director, 0491630572, lewis@harcourtmemorials.com.au
Phone # 02 9561 3048
Website: www.harcourtmemorials.com.au
Address: Suite 17, 8 Palfrey Lane, West Carlow, Sydney NSW 2156

Font styles to use
Serif
Decorative
Script

Requirements
Must have
• Would like to see the logo nicely implemented with a modern design. Embossed lettering would be a nice additive.

```html
<!DOCTYPE html>
<html lang="en">
<head>
<meta charset="utf-8">
<title>Harcourt Memorials – Business Card</title>
<link href="https://fonts.googleapis.com/css2?family=Cinzel:wght@400;600&family=Open+Sans:ital,wght@0,400;1,400&display=swap" rel="stylesheet">
<style>
  :root {
    --backdrop: #8e8f8f;
    --card-white: #f1f1f2;
    --gold: #c9a227;
    --ink: #1d1d1d;
    --text-grey: #3a3a3a;
  }
  * { margin: 0; padding: 0; box-sizing: border-box; }
  html, body {
    width: 1105px; height: 1200px; overflow: hidden;
    background: var(--backdrop);
  }
  .canvas { position: relative; width: 1105px; height: 1200px; }

  .card {
    position: absolute; left: 182px; width: 746px; height: 428px;
  }
  .card--front { top: 119px; background: var(--card-white); }
  .card--back { top: 635px; background: var(--gold); }

  .accent-bar {
    position: absolute; left: 0; top: 85px; width: 15px; height: 55px;
    background: var(--gold);
  }
  .person { position: absolute; left: 47px; top: 84px; }
  .person__name {
    font-family: "Cinzel", serif; font-weight: 600; font-size: 27px;
    color: var(--ink); letter-spacing: 0.5px; line-height: 1.1;
  }
  .person__role {
    font-family: "Cinzel", serif; font-weight: 400; font-size: 21px;
    color: var(--gold); letter-spacing: 0.5px; line-height: 1.2;
  }

  .address {
    position: absolute; left: 47px; top: 166px;
    font-family: "Open Sans", sans-serif; font-size: 19px; line-height: 28px;
    color: var(--text-grey);
  }
  .contacts {
    position: absolute; left: 47px; top: 234px; list-style: none;
    font-family: "Open Sans", sans-serif; font-size: 19px; line-height: 28px;
    color: var(--text-grey);
  }
  .contacts li { display: flex; align-items: center; gap: 10px; }
  .contacts svg { width: 16px; height: 16px; fill: var(--ink); flex: none; }

  .brand-name {
    position: absolute; text-align: center;
    font-family: "Cinzel", serif; font-weight: 600; color: var(--ink);
    line-height: 1.05; letter-spacing: 1px;
  }
  .card--front .brand-name { left: 420px; width: 300px; top: 160px; font-size: 44px; }
  .card--back .brand-name { left: 0; width: 746px; top: 120px; font-size: 56px; }

  .web-address {
    position: absolute; left: 0; width: 746px; top: 360px; text-align: center;
    font-family: "Open Sans", sans-serif; font-style: italic; font-size: 20px;
    color: var(--ink); letter-spacing: 1px;
  }
</style>
</head>
<body>
<main class="canvas">
  <section class="card card--front" aria-label="Card front">
    <div class="accent-bar"></div>
    <div class="person">
      <p class="person__name">Simon Harcourt</p>
      <p class="person__role">Operations Manager</p>
    </div>
    <p class="address">Suite 17, 8 Palfrey Lane<br>West Carlow, Sydney NSW 2156</p>
    <ul class="contacts">
      <li><svg viewBox="0 0 16 16"><path d="M3.5 1l2.5 3-1.5 2c1 2 3 4 5 5l2-1.5 3 2.5-1.5 2.5C8 15 1 8 1 2.5z"/></svg>02 9561 3048</li>
      <li><svg viewBox="0 0 16 16"><path d="M4 0h8a1 1 0 0 1 1 1v14a1 1 0 0 1-1 1H4a1 1 0 0 1-1-1V1a1 1 0 0 1 1-1zm1 2v10h6V2zm3 11a1 1 0 1 0 0 2 1 1 0 0 0 0-2z"/></svg>0417293086</li>
      <li><svg viewBox="0 0 16 16"><path d="M1 3h14v1L8 9 1 4zm0 2.5l7 5 7-5V13H1z"/></svg>simon@harcourtmemorials.com.au</li>
      <li><svg viewBox="0 0 16 16"><circle cx="8" cy="8" r="7.5"/></svg>www.harcourtmemorials.com.au</li>
    </ul>
    <p class="brand-name">Harcourt<br>Memorials</p>
  </section>

  <section class="card card--back" aria-label="Card back">
    <p class="brand-name">Harcourt<br>Memorials</p>
    <p class="web-address">www.harcourtmemorials.com.au</p>
  </section>
</main>
</body>
</html>
```